Business Card for Beach theme sports bar called MORVIN

I need a business card designed for our employees, front and back. This will be used by the employees of two business locations to hand out to customers. I've attached the previous business cards we used at one time for a Dantells (it is now Morvin). Looking for a fresh new card that is elegant but has character.

Target Market(s)

30-60, middle class

Contact Information for Business Card

We are a beach bar and sports bar. I am looking for an elegant business card with the front to have the MORVIN logo. Then on the back I need it to allow a space for employees to write their names and for them to write in their schedule. I have attached our old cards with our old name Dantells so you can pull everything we need on the cards. one thing is missing is we have another location at 2615 W Calder Ridge Rd with a number of 702-418-9053. Since we will use it for both locations it should allow the employee to circle or check mark the bar which they work at.

Font styles to use
Sans Serif

Requirements
Must have
• We are looking for some fresh ideas for the business card. Something that will really stick out to customers when the staff hands them out. Creativity will be looked at positively, but we still want it to look upscale and fun.

```html
<!DOCTYPE html>
<html lang="en">
<head>
<meta charset="utf-8">
<title>Morvin – Staff Business Card</title>
<link href="https://fonts.googleapis.com/css2?family=Raleway:wght@400;500&family=Montserrat:wght@500;600&display=swap" rel="stylesheet">
<style>
  :root {
    --bg: #2b2b2b;
    --card-black: #111111;
    --card-white: #f4f4f4;
    --ink: #141414;
    --mid-grey: #7d7d7d;
    --field: #ededed;
    --paper: #ffffff;
  }
  * { box-sizing: border-box; margin: 0; padding: 0; }
  html, body { width: 1200px; height: 960px; overflow: hidden; }
  body {
    background: var(--bg);
    font-family: "Raleway", sans-serif;
    display: flex; flex-direction: column; align-items: center; justify-content: center;
    gap: 44px;
  }
  .card {
    width: 720px; height: 411px; border-radius: 22px; overflow: hidden; position: relative;
    box-shadow: 0 10px 30px rgba(0,0,0,.45);
  }

  /* Front */
  .card--front { background: var(--card-black); }
  .front-pattern {
    position: absolute; inset: 0;
    background: radial-gradient(ellipse at 50% 40%, #262626 0%, #151515 55%, #0d0d0d 100%);
  }
  .brand {
    position: absolute; left: 50%; top: 50%; transform: translate(-50%, -50%);
    display: flex; align-items: center; gap: 18px;
  }
  .brand-dot { width: 26px; height: 26px; border-radius: 50%; border: 3px solid currentColor; }
  .brand-name {
    font-family: "Montserrat", sans-serif; font-weight: 600; font-size: 64px; letter-spacing: 8px;
  }
  .card--front .brand { color: var(--paper); }

  /* Back */
  .card--back { background: var(--card-white); color: var(--ink); }
  .back-brand { position: absolute; left: 46px; top: 66px; display: flex; align-items: center; gap: 12px; color: var(--ink); }
  .back-brand .brand-name { font-size: 40px; letter-spacing: 5px; }
  .back-brand .brand-dot { width: 18px; height: 18px; border-width: 2px; }

  .locations { position: absolute; left: 340px; top: 26px; display: flex; flex-direction: column; gap: 16px; }
  .location { display: flex; align-items: center; gap: 18px; }
  .check { width: 28px; height: 28px; border: 1.5px solid #bdbdbd; background: var(--paper); flex: none; }
  .location p { font-size: 15px; line-height: 1.35; color: #2a2a2a; }

  .band { position: absolute; left: 0; right: 0; top: 196px; height: 136px; background: var(--ink); }
  .bartender-row { position: absolute; left: 30px; right: 30px; top: 18px; height: 40px; display: flex; }
  .bartender-label {
    width: 150px; background: var(--mid-grey); color: var(--paper);
    font-size: 15px; font-weight: 500; letter-spacing: .5px;
    display: flex; align-items: center; padding-left: 16px;
  }
  .bartender-field { flex: 1; background: var(--field); }
  .days { position: absolute; left: 30px; right: 30px; top: 78px; display: flex; justify-content: space-between; }
  .day { display: flex; align-items: center; gap: 10px; color: var(--paper); font-size: 16px; }
  .day .check { border: none; width: 30px; height: 30px; }
  .band-rule { position: absolute; left: 0; right: 0; top: 340px; height: 3px; background: var(--ink); }

  .website {
    position: absolute; left: 0; right: 0; bottom: 24px; text-align: center;
    font-family: "Montserrat", sans-serif; font-weight: 600; font-size: 22px; letter-spacing: 7px; color: var(--ink);
  }
</style>
</head>
<body>
  <section class="card card--front">
    <div class="front-pattern" role="img" aria-label="Faint repeating palm leaf pattern"></div>
    <div class="brand">
      <span class="brand-dot"></span>
      <span class="brand-name">MORVIN</span>
    </div>
  </section>

  <section class="card card--back">
    <div class="back-brand">
      <span class="brand-dot"></span>
      <span class="brand-name">MORVIN</span>
    </div>

    <div class="locations">
      <div class="location">
        <span class="check"></span>
        <p>2615 W Calder Ridge Rd<br>702-418-9053</p>
      </div>
      <div class="location">
        <span class="check"></span>
        <p>3840 W Palmer Crest Rd<br>Las Vegas, NV 89152<br>702-531-6724</p>
      </div>
    </div>

    <div class="band">
      <div class="bartender-row">
        <div class="bartender-label">BARTENDER</div>
        <div class="bartender-field"></div>
      </div>
      <div class="days">
        <div class="day"><span class="check"></span>M</div>
        <div class="day"><span class="check"></span>T</div>
        <div class="day"><span class="check"></span>W</div>
        <div class="day"><span class="check"></span>Th</div>
        <div class="day"><span class="check"></span>F</div>
        <div class="day"><span class="check"></span>Sa</div>
        <div class="day"><span class="check"></span>Su</div>
      </div>
    </div>
    <div class="band-rule"></div>

    <p class="website">WWW.MORVINBAR.COM</p>
  </section>
</body>
</html>
```